I want a website to be designed for our new company, it's an import and export company for variety of things.

please see the attached Logo for our company and the Images for our different sections for our busienss

Target Market(s)

multiple

Coding

Coded - Design and coding required

Number of Pages Required

5+ page

Font styles to use
Sans Serif

Colors

Designer to choose colors to be used in the design.

Requirements
Must have
• KVR GLOBALINKS
• KVR globalinks Trading & Contracting provides various services. The Company offers infrastructure construction, oil, enegy and gas services, agricultural projects, real estate development, travel and tourism, and food processing and trading.
• Civil contracting for infrastructure, residential and heavy projects. Through its main subsidiaries; distribution of general food products, construction chemicals including corrosion inhibitors and electrical machinery; provides catering and travel agency services; ownership and operation of a school; offers human sources services including manpower supply.
• Drilling and Gold Mines Used Machinery, All Kinds of Construction Machinery, Drilling Machines are manufactured and sold.
Nice to have
• good designa and beautiful colours, it has too look professional

```html
<!DOCTYPE html>
<html lang="en">
<head>
<meta charset="utf-8">
<title>KVR GLOBALINKS</title>
<link rel="stylesheet" href="https://fonts.googleapis.com/css2?family=Montserrat:wght@400;500;600;700&display=swap">
<style>
:root{
  --orange:#f7931e;
  --dark:#262626;
  --ink:#2b2b2b;
  --muted:#666;
  --light:#bdbdbd;
  --white:#fff;
}
*{box-sizing:border-box;margin:0;padding:0}
html,body{width:1200px;height:4334px;overflow:hidden}
body{font-family:'Montserrat',sans-serif;background:var(--white);color:var(--ink);position:relative}
.abs{position:absolute}
.photo{position:absolute;display:block}

/* header */
.topbar{position:absolute;left:0;top:0;width:1200px;height:69px;background:rgba(20,20,20,.82);z-index:3}
.brand{position:absolute;left:96px;top:22px;display:flex;align-items:center;gap:8px;color:var(--white);font-size:14px;font-weight:700;letter-spacing:1px}
.brand i{width:18px;height:18px;border-radius:50%;background:var(--orange);display:block}
.social-top{position:absolute;right:90px;top:6px;display:flex;gap:8px}
.social-top span{width:18px;height:18px;border-radius:50%;background:#444;display:block}
.social-top span:first-child{background:var(--orange)}
.nav{position:absolute;right:92px;top:42px;display:flex;gap:46px;font-size:12px;color:#ddd}
.nav a{color:inherit;text-decoration:none}
.nav .active{border-left:2px solid var(--orange);padding-left:6px;color:var(--white)}

/* hero */
.hero{position:absolute;left:0;top:0;width:1200px;height:601px;background:linear-gradient(100deg,#3a1d12 0%,#8a3219 18%,#2e2a28 40%,#6d4a37 65%,#8d5e44 85%,#4a3226 100%)}
.hero-title{position:absolute;left:0;width:1200px;text-align:center;color:var(--white);font-weight:700}
.hero-title .kvr{display:block;color:var(--orange);font-size:56px;line-height:1;position:absolute;width:100%;top:222px}
.hero-title .name{display:block;font-size:70px;line-height:1;position:absolute;width:100%;top:280px}
.hero-tag{position:absolute;top:356px;width:1200px;text-align:center;color:var(--white);font-size:17px;letter-spacing:6px;font-weight:500}
.dots{position:absolute;top:524px;left:578px;display:flex;gap:7px}
.dots span{width:9px;height:9px;background:var(--white)}
.dots span:first-child{background:var(--orange)}

/* buttons */
.btn{position:absolute;display:flex;align-items:center;gap:8px;height:30px;padding:0 11px;font-size:11px;font-weight:600;color:var(--white);text-decoration:none;white-space:nowrap}
.btn b{width:15px;height:15px;border-radius:50%;display:inline-flex;align-items:center;justify-content:center}
.btn-dark{background:var(--dark)}
.btn-dark b{background:var(--orange)}
.btn-orange{background:var(--orange)}
.btn-orange b{background:var(--dark)}
.btn svg{width:7px;height:7px}

/* welcome */
.kicker{font-size:22px;color:var(--orange);font-weight:400}
.h2{font-size:40px;font-weight:700;line-height:1}
.para{font-size:13px;line-height:22.5px;color:var(--muted)}

/* services */
.dark-band{position:absolute;left:0;width:1200px;background:var(--dark)}
.center{text-align:center;width:1200px;left:0}
.card .cat{font-size:14px;color:#ccc}
.card .title{font-size:21px;color:var(--white);font-weight:500}
.card .text{font-size:10.5px;line-height:18px;color:#bbb}
.view-all{position:absolute;left:515px;top:2149px;width:168px;height:31px;background:var(--white);color:var(--ink);font-size:10px;font-weight:600;display:flex;align-items:center;justify-content:center}

/* news */
.news .title{font-size:18px;line-height:25px;color:var(--white)}
.news .text{font-size:10.5px;line-height:19px;color:#bbb}

/* footer */
.f-head{font-size:18px;color:#333}
.f-list{list-style:none;font-size:11px;color:#444}
.f-list li{position:absolute;white-space:nowrap}
.f-list li::before{content:"•";color:var(--orange);margin-right:3px}
.f-contact{font-size:11px;color:#444;line-height:15px}
.input{position:absolute;left:863px;width:243px;height:27px;border:1px solid #ccc;font-size:9px;color:#999;padding:8px 10px}
.subscribe{position:absolute;left:863px;top:4095px;width:243px;height:28px;background:var(--orange);color:var(--white);font-size:11px;display:flex;align-items:center;justify-content:center}
.copy{position:absolute;top:4188px;left:0;width:1200px;text-align:center;font-size:11px;color:#777}
.copy strong{color:#333;font-weight:600}
.social-foot{position:absolute;top:4219px;left:532px;display:flex;gap:8px}
.social-foot span{width:30px;height:30px;border-radius:50%;border:1px solid #ccc;display:block}
.social-foot span:first-child{background:var(--dark);border-color:var(--dark)}
</style>
</head>
<body>

<!-- Hero -->
<div class="hero" role="img" aria-label="Power drills in the foreground and a worker drilling into a brick wall"></div>
<header class="topbar">
  <div class="brand"><i></i>KVR GLOBALINKS</div>
  <div class="social-top"><span></span><span></span><span></span><span></span></div>
  <nav class="nav">
    <a class="active">Home</a><a>About Us</a><a>Services</a><a>News</a><a>Contact Us</a>
  </nav>
</header>
<h1 class="hero-title"><span class="kvr">KVR</span><span class="name">GLOBALINKS</span></h1>
<p class="hero-tag">A LARGE ASSORTMENT</p>
<div class="dots"><span></span><span></span><span></span></div>

<!-- Welcome -->
<section>
  <svg class="abs" style="left:638px;top:687px" width="562" height="368" aria-hidden="true"><polygon points="0,0 562,30 562,368 0,368" fill="var(--orange)"/></svg>
  <div class="photo" style="left:714px;top:746px;width:392px;height:378px;background:linear-gradient(135deg,#5c5c58,#8a8a80 45%,#c98a3a 70%,#3d4050)" role="img" aria-label="Two engineers in hard hats shaking hands on site"></div>
  <p class="abs kicker" style="left:93px;top:732px">Welcome To</p>
  <h2 class="abs h2" style="left:93px;top:766px;font-size:39px">KVR GLOBALINKS</h2>
  <p class="abs para" style="left:93px;top:820px;width:510px">Sed ut perspiciatis unde omnis iste natus error sit voluptatem accusantium doloremque laudantium, totam rem aperiam, eaque ipsa quae ab illo inventore veritatis et quasi architecto beatae vitae dicta sunt explicabo. Nemo enim ipsam voluptatem quia voluptas sit aspernatur aut odit aut fugit, sed quia consequuntur magni dolores eos qui ratione voluptatem sequi nesciunt. Neque porro quisquam est, qui dolorem ipsum quia dolor sit amet, consectetur, adipisci velit, sed quia non numquam eius modi tempora incidunt ut labore et dolore magnam aliquam quaerat voluptatem.</p>
  <a class="btn btn-dark" style="left:93px;top:1042px">READ MORE <b><svg viewBox="0 0 8 8"><path d="M2 1l3 3-3 3" stroke="#fff" stroke-width="1.5" fill="none"/></svg></b></a>
</section>

<!-- Services -->
<section class="dark-band" style="top:1212px;height:1038px"></section>
<p class="abs kicker center" style="top:1276px">KVR globalinks</p>
<h2 class="abs h2 center" style="top:1308px;color:var(--white)">OUR SERVICES</h2>
<p class="abs center" style="top:1356px;font-size:14px;color:#ccc">KVR globalinks Trading &amp; Contracting provides various services</p>

<div class="photo" style="left:93px;top:1422px;width:240px;height:158px;background:linear-gradient(180deg,#3f86d6,#8fb9e6 55%,#c46a2a 80%,#8a6a4a)" role="img" aria-label="Orange excavator on a construction site"></div>
<div class="photo" style="left:350px;top:1422px;width:242px;height:158px;background:linear-gradient(180deg,#1f5fb8,#6b8fba 50%,#3a3f46)" role="img" aria-label="Gas processing plant towers against blue sky"></div>
<div class="photo" style="left:608px;top:1422px;width:240px;height:158px;background:linear-gradient(180deg,#8fb3d6,#c9c2a8 45%,#4f6a3a 75%,#2c3a5c)" role="img" aria-label="Harvester and tractor in a farm field"></div>
<div class="photo" style="left:865px;top:1422px;width:241px;height:158px;background:linear-gradient(180deg,#3d7fd4,#8cb6e6 55%,#8a4a2e 80%,#5a3a2a)" role="img" aria-label="Tower crane over a building under construction"></div>

<div class="card">
  <p class="abs cat" style="left:93px;top:1588px">Infrastructure</p><p class="abs title" style="left:93px;top:1609px">Construction</p>
  <p class="abs cat" style="left:350px;top:1588px">Enegy and</p><p class="abs title" style="left:350px;top:1609px">Gas Services</p>
  <p class="abs cat" style="left:608px;top:1588px">Agricultural</p><p class="abs title" style="left:608px;top:1609px">Projects</p>
  <p class="abs cat" style="left:865px;top:1588px">Real Estate</p><p class="abs title" style="left:865px;top:1609px">Development</p>
  <p class="abs text" style="left:93px;top:1642px;width:236px">But I must explain to you how all this mistaken idea of denouncing pleasure and praising pain...</p>
  <p class="abs text" style="left:350px;top:1642px;width:236px">But I must explain to you how all this mistaken idea of denouncing pleasure and praising pain...</p>
  <p class="abs text" style="left:608px;top:1642px;width:236px">But I must explain to you how all this mistaken idea of denouncing pleasure and praising pain...</p>
  <p class="abs text" style="left:865px;top:1642px;width:236px">But I must explain to you how all this mistaken idea of denouncing pleasure and praising pain...</p>
</div>
<a class="btn btn-orange" style="left:93px;top:1709px">READ MORE <b><svg viewBox="0 0 8 8"><path d="M2 1l3 3-3 3" stroke="#fff" stroke-width="1.5" fill="none"/></svg></b></a>
<a class="btn btn-orange" style="left:350px;top:1709px">READ MORE <b><svg viewBox="0 0 8 8"><path d="M2 1l3 3-3 3" stroke="#fff" stroke-width="1.5" fill="none"/></svg></b></a>
<a class="btn btn-orange" style="left:608px;top:1709px">READ MORE <b><svg viewBox="0 0 8 8"><path d="M2 1l3 3-3 3" stroke="#fff" stroke-width="1.5" fill="none"/></svg></b></a>
<a class="btn btn-orange" style="left:865px;top:1709px">READ MORE <b><svg viewBox="0 0 8 8"><path d="M2 1l3 3-3 3" stroke="#fff" stroke-width="1.5" fill="none"/></svg></b></a>

<div class="photo" style="left:93px;top:1772px;width:240px;height:158px;background:linear-gradient(180deg,#d8dcc8,#8a9a6a 45%,#5c6a5a 75%,#3a3a3a)" role="img" aria-label="Traveller pulling a suitcase through an airport terminal"></div>
<div class="photo" style="left:350px;top:1772px;width:242px;height:158px;background:linear-gradient(135deg,#c9a66a,#7a5a3a 55%,#2a2a2a)" role="img" aria-label="Potatoes on a food processing conveyor"></div>
<div class="photo" style="left:608px;top:1772px;width:240px;height:158px;background:linear-gradient(180deg,#e8a65a,#c86a3a 45%,#3a3a4a 70%,#2a3a5a)" role="img" aria-label="Offshore oil platform at sunset"></div>
<div class="photo" style="left:865px;top:1772px;width:241px;height:158px;background:linear-gradient(180deg,#c8cace,#6a6c70 50%,#3a3c40)" role="img" aria-label="Group of workers in yellow hard hats"></div>

<div class="card">
  <p class="abs cat" style="left:93px;top:1939px">Travel and</p><p class="abs title" style="left:93px;top:1960px">Tourism</p>
  <p class="abs cat" style="left:350px;top:1939px">Food</p><p class="abs title" style="left:350px;top:1960px">Processing</p>
  <p class="abs cat" style="left:608px;top:1939px">Oil</p><p class="abs title" style="left:608px;top:1960px">Industries</p>
  <p class="abs cat" style="left:865px;top:1939px">Human</p><p class="abs title" style="left:865px;top:1960px">Sources Services</p>
  <p class="abs text" style="left:93px;top:1993px;width:236px">But I must explain to you how all this mistaken idea of denouncing pleasure and praising pain...</p>
  <p class="abs text" style="left:350px;top:1993px;width:236px">But I must explain to you how all this mistaken idea of denouncing pleasure and praising pain...</p>
  <p class="abs text" style="left:608px;top:1993px;width:236px">But I must explain to you how all this mistaken idea of denouncing pleasure and praising pain...</p>
  <p class="abs text" style="left:865px;top:1993px;width:236px">But I must explain to you how all this mistaken idea of denouncing pleasure and praising pain...</p>
</div>
<a class="btn btn-orange" style="left:93px;top:2060px">READ MORE <b><svg viewBox="0 0 8 8"><path d="M2 1l3 3-3 3" stroke="#fff" stroke-width="1.5" fill="none"/></svg></b></a>
<a class="btn btn-orange" style="left:350px;top:2060px">READ MORE <b><svg viewBox="0 0 8 8"><path d="M2 1l3 3-3 3" stroke="#fff" stroke-width="1.5" fill="none"/></svg></b></a>
<a class="btn btn-orange" style="left:608px;top:2060px">READ MORE <b><svg viewBox="0 0 8 8"><path d="M2 1l3 3-3 3" stroke="#fff" stroke-width="1.5" fill="none"/></svg></b></a>
<a class="btn btn-orange" style="left:865px;top:2060px">READ MORE <b><svg viewBox="0 0 8 8"><path d="M2 1l3 3-3 3" stroke="#fff" stroke-width="1.5" fill="none"/></svg></b></a>
<div class="view-all">VIEW ALL SERVICES</div>

<!-- Used machinery -->
<section>
  <svg class="abs" style="left:0;top:2336px" width="560" height="336" aria-hidden="true"><polygon points="0,0 560,0 560,336 0,336" fill="var(--orange)"/></svg>
  <div class="photo" style="left:76px;top:2397px;width:390px;height:459px;background:linear-gradient(180deg,#e8dcb8,#d6c28a 45%,#a88a4a 75%,#6a5a3a)" role="img" aria-label="Mining dump trucks in a dusty gold mine"></div>
  <div class="photo" style="left:473px;top:2701px;width:207px;height:155px;background:linear-gradient(135deg,#6a4a2a,#a87a4a 50%,#3a2a1a)" role="img" aria-label="Mine cart in an underground tunnel"></div>
  <div class="photo" style="left:687px;top:2701px;width:207px;height:155px;background:linear-gradient(135deg,#2a3a4a,#6a7a8a 50%,#1a2028)" role="img" aria-label="Drilling machinery inside a mine shaft"></div>
  <div class="photo" style="left:899px;top:2701px;width:207px;height:155px;background:linear-gradient(180deg,#cfd8c8,#4a6a3a 45%,#8a5a3a)" role="img" aria-label="Open pit mining site by a forest"></div>
  <p class="abs kicker" style="left:601px;top:2331px">Drilling and Gold Mines</p>
  <h2 class="abs h2" style="left:601px;top:2365px">USED MACHINERY</h2>
  <p class="abs" style="left:601px;top:2418px;width:510px;font-size:16px;font-weight:600;line-height:23px;color:#333">All Kinds of Construction Machinery, Drilling Machines are manufactured and sold.</p>
  <p class="abs para" style="left:601px;top:2476px;width:510px">Sed ut perspiciatis unde omnis iste natus error sit voluptatem accusantium doloremque laudantium, totam rem aperiam, eaque ipsa quae ab illo inventore veritatis et quasi architecto beatae vitae dicta sunt explicabo. Nemo enim ipsam voluptatem quia voluptas sit aspernatur aut odit aut fugit, sed quia consequuntur magni dolores eos qui ratione voluptatem sequi nesciunt. Neque porro quisquam est, qui dolorem ipsum</p>
  <a class="btn btn-dark" style="left:601px;top:2642px">READ MORE <b><svg viewBox="0 0 8 8"><path d="M2 1l3 3-3 3" stroke="#fff" stroke-width="1.5" fill="none"/></svg></b></a>
</section>

<!-- News -->
<section class="dark-band" style="top:2945px;height:598px"></section>
<p class="abs kicker center" style="top:3005px">KVR globalinks</p>
<h2 class="abs h2 center" style="top:3037px;color:var(--white)">LATEST NEWS</h2>
<div class="photo" style="left:93px;top:3098px;width:324px;height:201px;background:linear-gradient(135deg,#8a5a2a,#c89a5a 50%,#e8e0d0)" role="img" aria-label="Business meeting at a table with wood panelling"></div>
<div class="photo" style="left:438px;top:3098px;width:324px;height:201px;background:linear-gradient(135deg,#d8dce0,#8a9ab0 50%,#4a5a6a)" role="img" aria-label="People working at a desk with laptop and coffee"></div>
<div class="photo" style="left:783px;top:3098px;width:323px;height:201px;background:linear-gradient(180deg,#e0e4e8,#a8b0b8 45%,#6a7a5a 80%,#3a4a6a)" role="img" aria-label="Engineers in hard hats overlooking a construction site"></div>
<div class="news">
  <p class="abs title" style="left:93px;top:3310px;width:324px">There are many variations passages Lorem Ipsum</p>
  <p class="abs title" style="left:438px;top:3310px;width:324px">There are many variations passages Lorem Ipsum</p>
  <p class="abs title" style="left:783px;top:3310px;width:324px">There are many variations passages Lorem Ipsum</p>
  <p class="abs text" style="left:93px;top:3374px;width:324px">If you use this site regularly and would like to help keep the site on the Internet, please consider donating a small sum to help pay</p>
  <p class="abs text" style="left:438px;top:3374px;width:324px">If you use this site regularly and would like to help keep the site on the Internet, please consider donating a small sum to help pay</p>
  <p class="abs text" style="left:783px;top:3374px;width:324px">If you use this site regularly and would like to help keep the site on the Internet, please consider donating a small sum to help pay</p>
</div>
<a class="btn btn-orange" style="left:93px;top:3445px">READ MORE <b><svg viewBox="0 0 8 8"><path d="M2 1l3 3-3 3" stroke="#fff" stroke-width="1.5" fill="none"/></svg></b></a>
<a class="btn btn-orange" style="left:438px;top:3445px">READ MORE <b><svg viewBox="0 0 8 8"><path d="M2 1l3 3-3 3" stroke="#fff" stroke-width="1.5" fill="none"/></svg></b></a>
<a class="btn btn-orange" style="left:783px;top:3445px">READ MORE <b><svg viewBox="0 0 8 8"><path d="M2 1l3 3-3 3" stroke="#fff" stroke-width="1.5" fill="none"/></svg></b></a>

<!-- Gallery -->
<section aria-label="Gallery">
  <div class="photo" style="left:0;top:3543px;width:240px;height:176px;background:linear-gradient(180deg,#e8a65a,#c86a3a 45%,#2a3a5a)" role="img" aria-label="Oil platform at sunset"></div>
  <div class="photo" style="left:240px;top:3543px;width:240px;height:176px;background:linear-gradient(135deg,#4a6a8a,#8aa8c0 50%,#c8a82a)" role="img" aria-label="Yellow machinery in a snowy forest"></div>
  <div class="photo" style="left:480px;top:3543px;width:240px;height:176px;background:linear-gradient(135deg,#6a6a6a,#b8b8b8 50%,#8a8a8a)" role="img" aria-label="Aerial view of a large building complex"></div>
  <div class="photo" style="left:720px;top:3543px;width:240px;height:176px;background:linear-gradient(180deg,#3d7fd4,#8cb6e6 55%,#8a4a2e)" role="img" aria-label="Tower crane over a building"></div>
  <div class="photo" style="left:960px;top:3543px;width:240px;height:176px;background:linear-gradient(180deg,#c8cace,#6a6c70 50%,#3a3c40)" role="img" aria-label="Workers in yellow hard hats"></div>
  <div class="photo" style="left:0;top:3719px;width:240px;height:177px;background:linear-gradient(180deg,#d8dcc8,#8a9a6a 45%,#3a3a3a)" role="img" aria-label="Traveller in an airport terminal"></div>
  <div class="photo" style="left:240px;top:3719px;width:240px;height:177px;background:linear-gradient(180deg,#3f86d6,#8fb9e6 55%,#c46a2a)" role="img" aria-label="Orange excavator"></div>
  <div class="photo" style="left:480px;top:3719px;width:240px;height:177px;background:linear-gradient(135deg,#e8ece8,#5aa84a 50%,#2a6a2a)" role="img" aria-label="Rows of lettuce in a greenhouse"></div>
  <div class="photo" style="left:720px;top:3719px;width:240px;height:177px;background:linear-gradient(180deg,#6a8aa8,#2a5a6a 55%,#1a3a4a)" role="img" aria-label="Offshore drilling rig at sea"></div>
  <div class="photo" style="left:960px;top:3719px;width:240px;height:177px;background:linear-gradient(180deg,#1f5fb8,#6b8fba 50%,#3a3f46)" role="img" aria-label="Gas plant towers"></div>
</section>

<!-- Footer -->
<footer>
  <h3 class="abs f-head" style="left:93px;top:3978px;font-weight:400">Quick Links</h3>
  <h3 class="abs f-head" style="left:259px;top:3978px;font-weight:400">Services</h3>
  <h3 class="abs f-head" style="left:634px;top:3978px;font-weight:400">Contact Us</h3>
  <h3 class="abs f-head" style="left:863px;top:3978px;font-weight:400">Newsletter</h3>
  <ul class="f-list">
    <li style="left:93px;top:4019px">Home</li>
    <li style="left:93px;top:4048px">About Us</li>
    <li style="left:93px;top:4077px">Services</li>
    <li style="left:93px;top:4106px">News</li>
    <li style="left:93px;top:4135px">Contact Us</li>
    <li style="left:259px;top:4019px">Construction</li>
    <li style="left:259px;top:4048px">Oil Industry</li>
    <li style="left:259px;top:4077px">Enegy &amp; gas services</li>
    <li style="left:259px;top:4106px">Agricultural Projects</li>
    <li style="left:411px;top:4019px">Real Estate Development</li>
    <li style="left:411px;top:4048px">Travel &amp; Tourism</li>
    <li style="left:411px;top:4077px">Food Processing</li>
    <li style="left:411px;top:4106px">Human Sources Services</li>
  </ul>
  <svg class="abs" style="left:634px;top:4018px" width="10" height="13" viewBox="0 0 10 13" aria-hidden="true"><path d="M5 0a5 5 0 0 0-5 5c0 4 5 8 5 8s5-4 5-8a5 5 0 0 0-5-5z" fill="var(--orange)"/><circle cx="5" cy="5" r="2" fill="#fff"/></svg>
  <p class="abs f-contact" style="left:651px;top:4017px;width:170px">15 b Harbor Lane<br>Westbrook 2500</p>
  <svg class="abs" style="left:634px;top:4069px" width="11" height="11" viewBox="0 0 24 24" aria-hidden="true"><path d="M6.6 10.8a15 15 0 0 0 6.6 6.6l2.2-2.2a1 1 0 0 1 1-.25 11 11 0 0 0 3.6.6 1 1 0 0 1 1 1V20a1 1 0 0 1-1 1A17 17 0 0 1 3 4a1 1 0 0 1 1-1h3.5a1 1 0 0 1 1 1 11 11 0 0 0 .6 3.6 1 1 0 0 1-.25 1z" fill="var(--orange)"/></svg>
  <p class="abs f-contact" style="left:651px;top:4067px">+2 (555) 014 2200</p>
  <svg class="abs" style="left:634px;top:4112px" width="11" height="8" viewBox="0 0 11 8" aria-hidden="true"><rect width="11" height="8" fill="var(--orange)"/><path d="M0 0l5.5 4L11 0" stroke="#fff" fill="none"/></svg>
  <p class="abs f-contact" style="left:651px;top:4109px">info@kvrglobalinks.com</p>
  <div class="input" style="top:4024px">Enter Name:</div>
  <div class="input" style="top:4058px">Enter Email:</div>
  <div class="subscribe">Subscribe</div>
  <p class="copy">COPYRIGHT © 2020 <strong>KVR GLOBALINKS</strong>. ALL RIGHTS RESERVED.</p>
  <div class="social-foot"><span></span><span></span><span></span><span></span></div>
</footer>

</body>
</html>
```